Luxury Business Card Design for High-End Window Treatments

Gilded Slatworks
Custom Plantation Shutters & Architectural Shading Systems

⸻

BACK

Daniel Trevick
Owner

Custom Interior & Exterior Window Treatments

919-555-0148
gildedslatworks.com

I have included a picture that I’m hoping we can use on the back, but I’m also wondering if you can get rid of the ladder? Should we get rid of shutters , shades and blinds underneath Gilded Slatworks?

Target Market(s)

High-end residential homeowners, custom home builders, architects, interior designers, and luxury renovation clients seeking premium plantation shutters and motorized architectural shading systems.

Industry/Entity Type

Custom Window treatments

Contact Information for Business Card

Front Gilded Slatworks Custom Plantation Shutters Motorized Architectural Shading Systems BACK Daniel Trevick Owner 919-555-0148 GildedSlatworks.com Custom Interior & Exterior Window Treatments By Appointment

Requirements
Nice to have
• Not 100% sure on nice to halves or the color but you can definitely check out my website to get a better understanding of what I’m trying to do

```html
<!DOCTYPE html>
<html lang="en">
<head>
<meta charset="utf-8">
<title>Gilded Slatworks — Business Card</title>
<link rel="stylesheet" href="https://fonts.googleapis.com/css2?family=Libre+Baskerville:ital@0;1&family=Poppins:ital,wght@0,300;1,300&display=swap">
<style>
  :root {
    --page: #e9e7e2;
    --card-black: #121212;
    --gold: #f2d35c;
    --gold-soft: #c9b15a;
    --ivory: #efece4;
    --photo-dark: #2a2c2e;
    --photo-mid: #3a3d40;
    --line: #d8d6d0;
  }
  * { box-sizing: border-box; margin: 0; padding: 0; }
  html, body {
    width: 1200px; height: 1200px; overflow: hidden;
    background: var(--page);
  }
  .sheet {
    width: 1200px; height: 1200px;
    display: flex; flex-direction: column; align-items: center; justify-content: center;
    gap: 40px;
  }
  .card {
    position: relative; width: 900px; height: 540px; overflow: hidden;
    box-shadow: 0 8px 24px rgba(0,0,0,0.18);
  }

  /* Front */
  .card-front { background: var(--card-black); }
  .front-pattern {
    position: absolute; inset: 0;
    background: radial-gradient(ellipse at center, #1b1a16 0%, #121212 70%);
  }
  .front-brand {
    position: absolute; left: 0; right: 0; top: 205px;
    text-align: center;
    font-family: "Libre Baskerville", serif; font-weight: 400;
    font-size: 64px; line-height: 1.2; color: var(--gold);
  }
  .front-tagline {
    position: absolute; left: 0; right: 0; top: 466px;
    text-align: center;
    font-family: "Libre Baskerville", serif; font-size: 19px;
    letter-spacing: 1px; color: var(--gold);
  }

  /* Back */
  .card-back { background: var(--photo-dark); }
  .back-photo {
    position: absolute; inset: 0;
    background: linear-gradient(180deg, #34373a 0%, #2b2d2f 45%, #25282a 75%, #303330 100%);
  }
  .back-brand {
    position: absolute; right: 60px; top: 78px; width: 260px;
    text-align: center;
    font-family: "Libre Baskerville", serif; font-weight: 400;
    font-size: 38px; line-height: 1.25; color: var(--ivory);
  }
  .holder-name {
    position: absolute; left: 106px; top: 206px;
    font-family: "Libre Baskerville", serif; font-size: 40px; color: var(--ivory);
  }
  .holder-role {
    position: absolute; left: 106px; top: 256px;
    font-family: "Poppins", sans-serif; font-style: italic; font-weight: 300;
    font-size: 24px; color: var(--gold); letter-spacing: 1px;
    display: flex; align-items: flex-end; gap: 6px;
  }
  .holder-role .rule { width: 30px; height: 1px; background: var(--gold); margin-bottom: 7px; }

  .service-frame {
    position: absolute; left: 74px; top: 375px; right: 0; height: 94px;
    border-left: 1px solid var(--line); border-bottom: 1px solid var(--line);
  }
  .service-frame::before {
    content: ""; position: absolute; left: 0; top: 0; width: 314px; height: 1px; background: var(--line);
  }
  .service-text {
    position: absolute; left: 32px; top: 14px;
    font-family: "Libre Baskerville", serif; font-size: 19px; line-height: 1.5;
    color: var(--gold); letter-spacing: 0.5px;
  }

  .contact {
    position: absolute; left: 528px; top: 338px;
  }
  .contact-title {
    font-family: "Libre Baskerville", serif; font-style: italic;
    font-size: 18px; letter-spacing: 2px; color: var(--gold-soft);
  }
  .contact-rule { width: 30px; height: 1px; background: var(--ivory); margin: 12px 0 12px 2px; }
  .contact-line {
    font-family: "Poppins", sans-serif; font-weight: 300; font-size: 18px;
    letter-spacing: 4px; color: var(--ivory); line-height: 30px;
  }
</style>
</head>
<body>
  <main class="sheet">
    <section class="card card-front">
      <div class="front-pattern" role="img" aria-label="Fine gold quatrefoil dot pattern on black"></div>
      <h1 class="front-brand">Gilded<br>Slatworks</h1>
      <p class="front-tagline">Custom Plantation Shutters &amp; Motorized Architectural Shading Systems</p>
    </section>

    <section class="card card-back">
      <div class="back-photo" role="img" aria-label="Darkened photograph of a two-storey house with a screened porch"></div>
      <p class="back-brand">Gilded<br>Slatworks</p>
      <h2 class="holder-name">Daniel Trevick</h2>
      <p class="holder-role">Owner<span class="rule"></span></p>

      <div class="service-frame">
        <p class="service-text">Custom Interior &amp; Exterior<br>Window Treatments By Appointment</p>
      </div>

      <div class="contact">
        <p class="contact-title">Contact Info:</p>
        <div class="contact-rule"></div>
        <p class="contact-line">919-555-0148</p>
        <p class="contact-line">gildedslatworks.com</p>
      </div>
    </section>
  </main>
</body>
</html>
```